Souvenir and Health Food Products

We need a website designed for a Wholesaler & Distributor of Australia Made Souvenir & Health Food products. Our range includes many of Australia's leading brands: Willow's Cottage, Coastal by Design, Pebble & Fern, Tova Cosmetics, Pelurin, K D Leathergoods, Tresvik Leathergoods, Harwick's Salt & Clovertop Honey.

Design will be converted into a Dot Net Nuke skin and containers so needs to be compatible.

Needs to show off their products and be easy to navigate.

Would like a nice clean and corporate look.
Updates

Hi Everyone

All design concepts are with my client who has been extremely busy....hoping to get feedback from them this week.

Cheers
Maeve

Target Market(s)

Target market are retail shops looking to stock their products

Industry/Entity Type

Health

Number of Pages Required

2 pages

Requirements
Must have
• Proposed Site Map
• Home
• About Us
• Products
• Ordering
• Contact Us

• To be included in homepage design concept:

• Large area for a flash banner of rotating images on homepage
• Logo and Phone number in header for every page 07 5719 3462
• Some welcome text
• Some icons will need to be designed - Register for our newsletter and Contact Us
• Product category list on homepage – thumbnail image/name of category (click through)

• Product categories to use are:
• (allow for up to 15)
• • Willow’s Cottage (use p1000321/jpg)

• • Jojoba Oil (use TFP_0121.jpg))

• • Coastal by Design (use TFP_0077.jpg)

• Could you create a separate content page to show how products will look on category page with each product having a thumbnail image, description and Enquire now button.
Should not have
• No shopping cart or ecommerce needed

```html
<!DOCTYPE html>
<html lang="en">
<head>
<meta charset="utf-8">
<title>Kovara Trading – Website Concept</title>
<link href="https://fonts.googleapis.com/css2?family=Arimo:wght@400;700&display=swap" rel="stylesheet">
<style>
:root{
  --sky:#76bcdf;
  --blue:#0a7bbf;
  --blue-light:#2fa6e6;
  --paper:#f7f7f7;
  --card:#eeeeee;
  --text:#333;
  --gold:#f5c400;
}
*{box-sizing:border-box;margin:0;padding:0}
html,body{width:1200px;height:3086px;overflow:hidden}
body{background:var(--sky);font-family:"Arimo",Arial,sans-serif;color:var(--text);position:relative}
.page{position:absolute;left:43px;width:1111px;background:var(--paper);border-radius:0 22px 22px 22px;overflow:hidden}
.page-home{top:141px;height:1325px}
.page-products{top:1618px;height:1327px}
.site-header{position:absolute;left:0;top:0;width:100%;height:147px;background:#fff}
.header-wash{position:absolute;left:0;top:0;width:100%;height:147px;background:linear-gradient(100deg,#cfe7f6 0%,#ffffff 38%,#ffffff 70%,#d7ebf7 100%)}
.brand{position:absolute;left:20px;top:26px;display:flex;align-items:center;gap:10px;font-size:22px;font-weight:700;color:var(--blue)}
.brand-dot{width:16px;height:16px;border-radius:50%;background:var(--blue)}
.phone{position:absolute;right:28px;top:78px;font-size:31px;color:var(--blue);white-space:nowrap}
.main-nav{position:absolute;left:0;top:147px;width:100%;height:43px;background:linear-gradient(#2fb0ee,#0d86cc)}
.main-nav a{position:absolute;top:0;height:43px;line-height:43px;color:#fff;text-decoration:none;font-size:16px;text-align:center;width:140px;margin-left:-70px}
.main-nav a.active{background:var(--paper);color:var(--blue)}
.main-nav a.active.fill{background:linear-gradient(#5cc3f2,#36aee8);color:#fff}
.crumb{position:absolute;left:26px;display:flex;align-items:center;gap:6px;font-size:13px;color:var(--blue);white-space:nowrap}
.crumb b{color:#111;font-weight:400}
.banner{position:absolute;left:26px;top:250px;width:754px;height:278px;background:linear-gradient(90deg,#6aa84f 0%,#d9e7c8 30%,#f3e3d5 45%,#ffffff 75%)}
.banner-cta{position:absolute;left:526px;top:456px;width:254px;height:72px;background:var(--blue);color:#fff;font-size:13px;display:flex;align-items:center;justify-content:center;gap:10px;white-space:nowrap}
.newsletter{position:absolute;left:804px;top:250px;width:284px;height:211px;background:var(--blue);border-radius:4px;color:#fff;padding:20px 26px}
.newsletter h3{font-size:21px;font-weight:700;letter-spacing:.3px;padding-bottom:15px;border-bottom:1px solid #7cc0e8;white-space:nowrap}
.newsletter label{display:block;font-size:10px;margin-top:22px}
.newsletter .field{height:18px;background:#fff;margin-top:6px}
.newsletter .submit{position:absolute;right:30px;top:144px;width:82px;height:30px;background:linear-gradient(#fff,#ddd);border:1px solid #555;border-radius:3px;color:#222;font-size:13px;text-align:center;line-height:28px}
.newsletter hr{position:absolute;left:26px;right:26px;top:195px;border:0;border-top:1px solid #7cc0e8}
.contact-btn{position:absolute;display:flex;align-items:center;justify-content:center;gap:28px;background:linear-gradient(#fff,#eef3f6);border:2px solid #9fd0ee;color:var(--blue);font-size:25px;white-space:nowrap}
.section-title{position:absolute;font-size:29px;font-weight:400;color:var(--blue);white-space:nowrap}
.category-card{position:absolute;background:var(--card);padding:20px 28px}
.category-card h4{font-size:25px;font-weight:400;color:var(--blue);white-space:nowrap}
.category-card svg.go{position:absolute;right:18px;top:12px}
.category-card .thumb{position:absolute;left:50%;transform:translateX(-50%);border-radius:6px}
.welcome{position:absolute;left:26px;top:1025px;width:1062px;border-left:5px solid var(--blue);padding:6px 0 6px 30px;font-size:15.2px;line-height:27px;color:#222}
.site-footer{position:absolute;left:0;width:100%;height:82px;background:var(--blue);color:#fff;text-align:right;padding:16px 22px;font-size:12.5px;line-height:32px;white-space:nowrap}
.site-footer .here{color:#111}
.side-box{position:absolute;left:24px;top:251px;width:276px;height:279px;background:var(--blue);color:#fff}
.side-box h3{height:56px;line-height:56px;text-align:center;font-size:20px;font-weight:400;border-bottom:1px solid #5eb3e6}
.side-box ul{list-style:none;padding:30px 0 0 32px}
.side-box li{font-size:19px;line-height:37px;display:flex;align-items:center;gap:16px;white-space:nowrap}
.side-box li::before{content:"";width:9px;height:9px;background:#fff}
.side-box li.current{color:var(--gold)}
.catalogue{position:absolute;left:332px;top:251px;width:755px;height:963px;background:var(--card)}
.catalogue-head{height:87px;color:#fff;font-size:44px;font-weight:700;padding:14px 30px;background:linear-gradient(#2aa1df,#1b8fd0)}
.catalogue-photo{height:123px;background:linear-gradient(90deg,#f3e6a3,#ffe9a8 30%,#e7e0c8 60%,#d9a100 90%)}
.product-grid{position:absolute;left:42px;top:250px;width:670px;height:700px}
.product-grid .divider{position:absolute;left:335px;top:-20px;width:1px;height:720px;background:#8fc3e3}
.product{position:absolute;width:290px;height:204px}
.product .pic{position:absolute;left:8px;top:28px;width:160px;height:158px;background:linear-gradient(90deg,#e5b400 0%,#b8102a 35%,#c01b30 60%,#f0b000 100%);border-radius:4px}
.product .info{position:absolute;left:190px;top:40px;font-size:15px;color:#555;line-height:29px;white-space:nowrap}
.product .order{position:absolute;left:190px;top:128px;width:107px;height:40px;border:2px solid #86bfe0;border-radius:4px;background:#fff;color:var(--blue);font-size:17px;text-align:center;line-height:36px}
.product.rule{border-bottom:1px solid #8fc3e3}
</style>
</head>
<body>

<section class="page page-home">
  <header class="site-header">
    <div class="header-wash" role="img" aria-label="Soft blue decorative wash"></div>
    <div class="brand"><span class="brand-dot"></span>Kovara Trading</div>
    <div class="phone">Call&nbsp; 07 5719 3462</div>
  </header>
  <nav class="main-nav">
    <a class="active" style="left:231px">Home</a>
    <a style="left:368px">About Us</a>
    <a style="left:521px">Products</a>
    <a style="left:670px">Ordering</a>
    <a style="left:828px">Contact Us</a>
  </nav>
  <div class="crumb" style="top:211px">
    <svg width="16" height="14" viewBox="0 0 16 14"><path d="M2 7 L8 1 L14 7 M4 6 V13 H12 V6" fill="none" stroke="var(--blue)" stroke-width="1.8"/></svg>HOME
  </div>

  <div class="banner" role="img" aria-label="Rotating banner photo: green leaves beside natural skincare"></div>
  <div class="banner-cta">CHECK OUR NEW PRODUCTS
    <svg width="26" height="26" viewBox="0 0 26 26"><circle cx="13" cy="13" r="11" fill="none" stroke="#fff" stroke-width="2"/><path d="M7 13 H18 M13 8 L18 13 L13 18" fill="none" stroke="#fff" stroke-width="2"/></svg>
  </div>

  <form class="newsletter">
    <h3>Sign up for newsletter</h3>
    <label>* Please type in your email address</label>
    <div class="field"></div>
    <div class="submit">SUBMIT</div>
    <hr>
  </form>
  <div class="contact-btn" style="left:804px;top:480px;width:284px;height:52px">
    <svg width="36" height="24" viewBox="0 0 36 24"><rect x="1" y="1" width="34" height="22" fill="var(--blue)"/><path d="M1 1 L18 14 L35 1" fill="none" stroke="#fff" stroke-width="2"/></svg>CONTACT US
  </div>

  <h2 class="section-title" style="left:29px;top:563px">Product Category</h2>

  <article class="category-card" style="left:26px;top:644px;width:337px;height:257px">
    <h4>Willow’s Cottage</h4>
    <svg class="go" width="44" height="44" viewBox="0 0 44 44"><circle cx="22" cy="22" r="19" fill="none" stroke="var(--blue)" stroke-width="3"/><path d="M11 22 H31 M23 14 L31 22 L23 30" fill="none" stroke="var(--blue)" stroke-width="3"/></svg>
    <div class="thumb" role="img" aria-label="Jars and bottles of herbal health products" style="top:96px;width:240px;height:120px;background:linear-gradient(90deg,#2c6b4a,#e4d89a,#2f6f55,#d8cf90)"></div>
  </article>
  <article class="category-card" style="left:387px;top:644px;width:338px;height:257px">
    <h4>Coastal by Design</h4>
    <svg class="go" width="44" height="44" viewBox="0 0 44 44"><circle cx="22" cy="22" r="19" fill="none" stroke="var(--blue)" stroke-width="3"/><path d="M11 22 H31 M23 14 L31 22 L23 30" fill="none" stroke="var(--blue)" stroke-width="3"/></svg>
    <div class="thumb" role="img" aria-label="Boxed soaps and skincare gift packs" style="top:78px;width:150px;height:150px;background:linear-gradient(135deg,#e4dcc0,#7c9a3c,#4f6b2a)"></div>
  </article>
  <article class="category-card" style="left:751px;top:644px;width:337px;height:257px">
    <h4>Jojoba Oil</h4>
    <svg class="go" width="44" height="44" viewBox="0 0 44 44"><circle cx="22" cy="22" r="19" fill="none" stroke="var(--blue)" stroke-width="3"/><path d="M11 22 H31 M23 14 L31 22 L23 30" fill="none" stroke="var(--blue)" stroke-width="3"/></svg>
    <div class="thumb" role="img" aria-label="Bottles and boxes of jojoba oil" style="top:74px;width:160px;height:160px;background:linear-gradient(90deg,#e5b400,#b8102a 40%,#c01b30 60%,#f0b000)"></div>
  </article>

  <h2 class="section-title" style="left:33px;top:937px">et iuquam ut</h2>
  <p class="welcome">Lorem ipsum dolor sit amet, consectetur adipiscing elit. Sed dictum mollis metus, sed varius leo convallis ac. Nulla id augue eu leo tristique consectetur et sit amet lectus. Cum sociis natoque penatibus et magnis dis parturient montes, nascetur ridiculus mus. Sed sed turpis ipsum. Curabitur ipsum velit, vestibulum id bibendum at, eleifend at diam. Quisque cursus tincidunt dignissim. Morbi semper bibendum nisi, blandi hendrerit ligula dictum et. Praesent gravida eros et leo pretium vel accumsan sem feugiat. Quisque vitae sapien vel tortor tempor consecte r sed eget felis. Proin lectus nisi, congue eget bibendum vitae, aliquam nec dolor. Aliquam porta enim vel sapien placerat condimentum. M ecenas consequat viverra dolor, ut tempus ligula varius at. Pellentesque gravida di</p>

  <footer class="site-footer" style="top:1244px">
    | <span class="here">Home</span> | About Us | Products | Ordering | Contact Us |<br>
    Copyright @ Kovara Trading 2009
  </footer>
</section>

<section class="page page-products">
  <header class="site-header">
    <div class="header-wash" role="img" aria-label="Soft blue decorative wash"></div>
    <div class="brand"><span class="brand-dot"></span>Kovara Trading</div>
    <div class="phone">Call&nbsp; 07 5719 3462</div>
  </header>
  <nav class="main-nav">
    <a style="left:231px">Home</a>
    <a style="left:368px">About Us</a>
    <a class="active fill" style="left:521px">Products</a>
    <a style="left:670px">Ordering</a>
    <a style="left:828px">Contact Us</a>
  </nav>
  <div class="crumb" style="top:212px">
    <svg width="16" height="14" viewBox="0 0 16 14"><path d="M2 7 L8 1 L14 7 M4 6 V13 H12 V6" fill="none" stroke="var(--blue)" stroke-width="1.8"/></svg>HOME | Products | <b>Jojoba Oil</b>
  </div>

  <aside class="side-box">
    <h3>CATEGORY LIST</h3>
    <ul>
      <li class="current">Jojoba Oil</li>
      <li>Willow’s Cottage</li>
      <li>Coastal by Design</li>
    </ul>
    <div class="contact-btn" style="left:24px;top:221px;width:228px;height:42px;font-size:20px;gap:24px">
      <svg width="28" height="19" viewBox="0 0 36 24"><rect x="1" y="1" width="34" height="22" fill="var(--blue)"/><path d="M1 1 L18 14 L35 1" fill="none" stroke="#fff" stroke-width="2"/></svg>CONTACT US
    </div>
  </aside>

  <article class="category-card" style="left:24px;top:559px;width:276px;height:209px;padding:16px 24px">
    <h4 style="font-size:20px">Coastal by Design</h4>
    <svg class="go" width="38" height="38" viewBox="0 0 44 44" style="top:8px;right:14px"><circle cx="22" cy="22" r="19" fill="none" stroke="var(--blue)" stroke-width="3"/><path d="M11 22 H31 M23 14 L31 22 L23 30" fill="none" stroke="var(--blue)" stroke-width="3"/></svg>
    <div class="thumb" role="img" aria-label="Boxed soaps and skincare gift packs" style="top:62px;width:120px;height:120px;background:linear-gradient(135deg,#e4dcc0,#7c9a3c,#4f6b2a)"></div>
  </article>
  <article class="category-card" style="left:24px;top:801px;width:276px;height:211px;padding:16px 24px">
    <h4 style="font-size:20px">Willow’s Cottage</h4>
    <svg class="go" width="38" height="38" viewBox="0 0 44 44" style="top:8px;right:14px"><circle cx="22" cy="22" r="19" fill="none" stroke="var(--blue)" stroke-width="3"/><path d="M11 22 H31 M23 14 L31 22 L23 30" fill="none" stroke="var(--blue)" stroke-width="3"/></svg>
    <div class="thumb" role="img" aria-label="Jars and bottles of herbal health products" style="top:80px;width:200px;height:100px;background:linear-gradient(90deg,#2c6b4a,#e4d89a,#2f6f55,#d8cf90)"></div>
  </article>

  <main class="catalogue">
    <h1 class="catalogue-head">Jojoba Oil</h1>
    <div class="catalogue-photo" role="img" aria-label="Close-up of golden jojoba oil bottles"></div>
    <div class="product-grid">
      <div class="divider"></div>
      <div class="product rule" style="left:0;top:0"><div class="pic" role="img" aria-label="Jojoba oil bottles and box"></div><div class="info">Jojoba oil<br>ITEM: 25465<br>PRICE: $15.00</div><div class="order">ORDER</div></div>
      <div class="product rule" style="left:380px;top:0"><div class="pic" role="img" aria-label="Jojoba oil bottles and box"></div><div class="info">Jojoba oil<br>ITEM: 25465<br>PRICE: $15.00</div><div class="order">ORDER</div></div>
      <div class="product rule" style="left:0;top:204px"><div class="pic" role="img" aria-label="Jojoba oil bottles and box"></div><div class="info">Jojoba oil<br>ITEM: 25465<br>PRICE: $15.00</div><div class="order">ORDER</div></div>
      <div class="product rule" style="left:380px;top:204px"><div class="pic" role="img" aria-label="Jojoba oil bottles and box"></div><div class="info">Jojoba oil<br>ITEM: 25465<br>PRICE: $15.00</div><div class="order">ORDER</div></div>
      <div class="product" style="left:0;top:410px"><div class="pic" role="img" aria-label="Jojoba oil bottles and box"></div><div class="info">Jojoba oil<br>ITEM: 25465<br>PRICE: $15.00</div><div class="order">ORDER</div></div>
      <div class="product" style="left:380px;top:410px"><div class="pic" role="img" aria-label="Jojoba oil bottles and box"></div><div class="info">Jojoba oil<br>ITEM: 25465<br>PRICE: $15.00</div><div class="order">ORDER</div></div>
    </div>
  </main>

  <footer class="site-footer" style="top:1245px">
    | Home | About Us | <span class="here">Products</span> | Ordering | Contact Us |<br>
    Copyright @ Kovara Trading 2009
  </footer>
</section>

</body>
</html>
```